bRu Design Group - architect web site

need a web site to permit potential clients to view our portfolio of work.

Will need lots of photos included.

Industry/Entity Type

Architect

Coding

Coded - Design and coding required

Number of Pages Required

5+ page

Font styles to use
Sans Serif

Requirements
Must have
• photos should be organized by project - perhaps a summary of photos and then click to enlarge? should be simple to operate. should be able to separate interior design from architecture.
• needs to be easy to add more photos in the future.

```html
<!DOCTYPE html>
<html lang="en">
<head>
<meta charset="utf-8">
<title>bRu Design Group</title>
<link href="https://fonts.googleapis.com/css2?family=Raleway:wght@400;500;600;700&family=Open+Sans:wght@400;600&display=swap" rel="stylesheet">
<style>
  :root {
    --white: #ffffff;
    --ink: #2b2b2b;
    --muted: #7a7a7a;
    --nav-active: #d9d9d9;
    --portfolio-bg: #f1f1f1;
    --news-bg: #1f1f1f;
    --footer-bg: #141414;
    --field-bg: #2e2e2e;
    --button-bg: #8a8a8a;
    --social-bg: #4a6a8a;
    --footer-text: #9a9a9a;
    --footer-strong: #d0d0d0;
  }
  * { box-sizing: border-box; margin: 0; padding: 0; }
  html, body { width: 870px; height: 1200px; overflow: hidden; }
  body { background: var(--white); color: var(--ink); font-family: "Open Sans", Arial, sans-serif; position: relative; }

  /* Header */
  .site-header { position: absolute; top: 0; left: 0; width: 870px; height: 78px; background: var(--white); }
  .brand { position: absolute; left: 34px; top: 30px; font-family: "Raleway", Arial, sans-serif; font-weight: 700; font-size: 17px; color: var(--ink); letter-spacing: .5px; line-height: 20px; white-space: nowrap; }
  .main-nav { position: absolute; right: 20px; top: 30px; display: flex; }
  .main-nav a { font-family: "Raleway", Arial, sans-serif; font-size: 10px; font-weight: 600; color: var(--ink); text-decoration: none; padding: 6px 11px; text-transform: uppercase; letter-spacing: .5px; }
  .main-nav a.is-active { background: var(--nav-active); }

  /* Hero */
  .hero { position: absolute; top: 78px; left: 0; width: 870px; height: 400px; }
  .hero-photo { width: 100%; height: 100%; background: linear-gradient(160deg, #f4f4f2 0%, #dcdcd8 40%, #9a9a94 70%, #6e5a44 100%); }
  .hero-caption { position: absolute; left: 92px; top: 190px; background: rgba(255,255,255,.55); padding: 8px 16px; font-family: "Raleway", Arial, sans-serif; font-size: 30px; font-weight: 500; color: var(--white); letter-spacing: 1px; white-space: nowrap; }
  .slider-arrow { position: absolute; width: 24px; height: 24px; border-radius: 50%; top: 192px; display: flex; align-items: center; justify-content: center; }
  .slider-arrow.prev { left: 18px; background: rgba(0,0,0,.75); }
  .slider-arrow.next { right: 18px; background: var(--white); }

  /* Welcome */
  .welcome { position: absolute; top: 478px; left: 0; width: 870px; height: 145px; text-align: center; padding-top: 42px; }
  .section-title { font-family: "Raleway", Arial, sans-serif; font-size: 18px; font-weight: 600; letter-spacing: .5px; color: var(--ink); text-transform: uppercase; }
  .welcome-text { width: 700px; margin: 18px auto 0; font-size: 9.5px; line-height: 1.6; color: var(--muted); }

  /* Portfolio */
  .portfolio { position: absolute; top: 623px; left: 0; width: 870px; height: 385px; background: var(--portfolio-bg); text-align: center; padding-top: 26px; }
  .portfolio-intro { width: 690px; margin: 10px auto 0; font-size: 9.5px; line-height: 1.6; color: var(--muted); }
  .portfolio-grid { position: absolute; left: 80px; top: 104px; width: 710px; display: grid; grid-template-columns: repeat(4, 164px); column-gap: 18px; row-gap: 16px; }
  .project-card { display: flex; flex-direction: column; }
  .project-photo { width: 164px; height: 100px; border: 3px solid var(--white); box-shadow: 0 1px 3px rgba(0,0,0,.2); }
  .project-name { margin-top: 6px; font-size: 8.5px; color: var(--muted); white-space: nowrap; }
  .grid-arrow { position: absolute; top: 210px; }
  .grid-arrow.prev { left: 42px; }
  .grid-arrow.next { right: 42px; }
  .tone-a { background: linear-gradient(180deg, #b8c4cc, #7a7f78); }
  .tone-b { background: linear-gradient(180deg, #c9b79a, #6f5d48); }
  .tone-c { background: linear-gradient(180deg, #e8e6e0, #a6a29a); }
  .tone-d { background: linear-gradient(180deg, #a8b6c0, #cfc7b6); }
  .tone-e { background: linear-gradient(180deg, #9a7a56, #d8cbb4); }
  .tone-f { background: linear-gradient(180deg, #b9b2a6, #6a6156); }
  .tone-g { background: linear-gradient(180deg, #efefec, #9e9a92); }
  .tone-h { background: linear-gradient(180deg, #d4d9dc, #8c8f88); }

  /* Newsletter */
  .newsletter { position: absolute; top: 1008px; left: 0; width: 870px; height: 152px; background: var(--news-bg); text-align: center; padding-top: 26px; color: var(--white); }
  .newsletter-title { font-family: "Raleway", Arial, sans-serif; font-size: 18px; font-weight: 500; letter-spacing: .5px; text-transform: uppercase; }
  .newsletter-sub { font-size: 8px; color: #bdbdbd; margin-top: 6px; text-transform: uppercase; letter-spacing: 1px; }
  .signup-form { display: flex; justify-content: center; gap: 12px; margin-top: 18px; }
  .field { width: 190px; height: 30px; background: var(--field-bg); border: 1px solid #444; color: #cfcfcf; font-size: 9px; text-align: left; padding: 9px 10px; }
  .submit { width: 130px; height: 30px; background: var(--button-bg); color: var(--white); font-family: "Raleway", Arial, sans-serif; font-weight: 600; font-size: 12px; letter-spacing: 1px; display: flex; align-items: center; justify-content: center; }

  /* Footer */
  .site-footer { position: absolute; top: 1160px; left: 0; width: 870px; height: 40px; background: var(--footer-bg); display: flex; align-items: center; justify-content: space-between; padding: 0 22px; font-size: 8px; color: var(--footer-text); }
  .footer-links b { color: var(--footer-strong); font-weight: 600; }
  .footer-right { display: flex; align-items: center; gap: 5px; }
  .social { width: 14px; height: 14px; background: var(--social-bg); }
  .footer-brand { margin-left: 10px; font-weight: 600; color: var(--footer-strong); }
</style>
</head>
<body>

<header class="site-header">
  <div class="brand">bRu Design Group</div>
  <nav class="main-nav">
    <a href="#" class="is-active">Home</a>
    <a href="#">About Us</a>
    <a href="#">Services</a>
    <a href="#">Portfolio</a>
    <a href="#">News</a>
    <a href="#">Contact Us</a>
  </nav>
</header>

<section class="hero">
  <div class="hero-photo" role="img" aria-label="Bright white interior with a staircase, dark stone floor and tall windows"></div>
  <div class="hero-caption">ARCHITECT TO EXHIBIT</div>
  <div class="slider-arrow prev">
    <svg width="10" height="10" viewBox="0 0 10 10"><path d="M6.5 1.5 L3 5 L6.5 8.5" fill="none" stroke="#fff" stroke-width="1.6"/></svg>
  </div>
  <div class="slider-arrow next">
    <svg width="10" height="10" viewBox="0 0 10 10"><path d="M3.5 1.5 L7 5 L3.5 8.5" fill="none" stroke="#222" stroke-width="1.6"/></svg>
  </div>
</section>

<section class="welcome">
  <h2 class="section-title">Welcome to bRu Design Group</h2>
  <p class="welcome-text">We design homes, studios and public spaces that balance light, material and proportion. Each project begins with careful listening and ends with a building that feels calm, useful and lasting. Our team handles architecture and interior design from first sketch to final handover, working closely with clients and builders at every stage of the process.</p>
</section>

<section class="portfolio">
  <h2 class="section-title">Our Portfolio</h2>
  <p class="portfolio-intro">Browse selected projects below, sorted by architecture and interior design. Click any photo to open the full project gallery with plans and details.</p>

  <svg class="grid-arrow prev" width="12" height="16" viewBox="0 0 12 16"><path d="M9 2 L3 8 L9 14" fill="none" stroke="#333" stroke-width="2"/></svg>
  <svg class="grid-arrow next" width="12" height="16" viewBox="0 0 12 16"><path d="M3 2 L9 8 L3 14" fill="none" stroke="#333" stroke-width="2"/></svg>

  <div class="portfolio-grid">
    <div class="project-card"><div class="project-photo tone-a" role="img" aria-label="Modern house exterior by the water"></div><span class="project-name">Lakeside house, North Shore</span></div>
    <div class="project-card"><div class="project-photo tone-b" role="img" aria-label="Warm wooden interior with large windows"></div><span class="project-name">Hillside retreat interior</span></div>
    <div class="project-card"><div class="project-photo tone-c" role="img" aria-label="White open plan kitchen"></div><span class="project-name">Open plan family kitchen</span></div>
    <div class="project-card"><div class="project-photo tone-d" role="img" aria-label="Living room with garden view"></div><span class="project-name">Garden view living room</span></div>
    <div class="project-card"><div class="project-photo tone-e" role="img" aria-label="Room with exposed timber roof beams"></div><span class="project-name">Timber beam great room</span></div>
    <div class="project-card"><div class="project-photo tone-f" role="img" aria-label="Stone residence with terrace"></div><span class="project-name">Stone terrace residence</span></div>
    <div class="project-card"><div class="project-photo tone-g" role="img" aria-label="Kitchen with marble island"></div><span class="project-name">Marble kitchen island</span></div>
    <div class="project-card"><div class="project-photo tone-h" role="img" aria-label="Lounge with corner windows"></div><span class="project-name">Corner window lounge</span></div>
  </div>
</section>

<section class="newsletter">
  <h2 class="newsletter-title">Sign up below to get news</h2>
  <p class="newsletter-sub">Subscribe to our mailing list</p>
  <div class="signup-form">
    <div class="field">Name</div>
    <div class="field">Email Address</div>
    <div class="submit">SUBMIT</div>
  </div>
</section>

<footer class="site-footer">
  <span class="footer-links">© 2024 bRu Design Group. All Rights Reserved. <b>Privacy Policy</b> | <b>Terms of Service</b></span>
  <div class="footer-right">
    <span class="social"></span>
    <span class="social"></span>
    <span class="social"></span>
    <span class="social"></span>
    <span class="social"></span>
    <span class="footer-brand">bRu</span>
  </div>
</footer>

</body>
</html>
```